bamboo kettle vietnamese restaurant in need of a new menu

a family owned vietnamese restaurant in need of a new menu design that is fun, classy, and yet simple. menu that will catch the customers eyes. easy to read yet flows nicely. like to use the color green (basil green color) creme yellow and maroon. open to other colors as long as it looks nice together. our restaurant is family oriented, casual yet has a nice ambiance atmosphere.
prefer 11x17 portrait double sided. attached is our menu with the current price updated so use the info on this to start creating! looking for something unique, professional and one of a kind menu!
Updates
please use your own creative layout and design. we are open to ideas. the files uploaded are the updated prices and the logo is to use whichever one you feel goes with the menu.
Reason: don't see anything we like so far...please be creative!
Target Market(s)
restaurant consumers
Industry/Entity Type
Restaurant
Look and feel

```html
<!DOCTYPE html>
<html lang="en">
<head>
<meta charset="utf-8">
<title>Bamboo Kettle Menu</title>
<link href="https://fonts.googleapis.com/css2?family=League+Gothic&family=Pathway+Gothic+One&display=swap" rel="stylesheet">
<style>
:root{
  --basil:#5bb530;
  --basil-light:#86c44a;
  --ink:#231f20;
  --muted:#8a8a8a;
  --paper:#ffffff;
  --flame:#f06a1d;
}
*{margin:0;padding:0;box-sizing:border-box}
html,body{width:1200px;height:777px;overflow:hidden;background:var(--paper)}
.menu{position:relative;width:1200px;height:777px;overflow:hidden;background:var(--paper);color:var(--ink);font-family:"Pathway Gothic One",sans-serif;text-transform:uppercase}
.leaf{position:absolute;border-radius:50%;background:radial-gradient(closest-side,rgba(134,196,74,.26),rgba(134,196,74,0))}

.head{position:absolute;display:flex;align-items:flex-start;gap:5px}
.head.stack{flex-direction:column;align-items:center;gap:2px}
.head.stack.left{align-items:flex-start}
.section-title{font-family:"League Gothic",sans-serif;color:var(--basil);font-weight:400;line-height:.86;letter-spacing:.5px;white-space:nowrap}
.head-text{display:flex;flex-direction:column;padding-top:2px}
.subtitle{font-family:"League Gothic",sans-serif;color:var(--ink);font-weight:400;font-size:16px;line-height:15px;letter-spacing:.3px;white-space:nowrap}
.note{font-size:9.5px;line-height:11px;color:var(--ink)}
.note.faint{color:var(--muted);font-size:10px}
.intro{position:absolute;font-size:9.5px;line-height:11px}

.list{position:absolute;list-style:none}
.item{display:flex;margin-bottom:5px}
.num{flex:0 0 18px;font-family:"League Gothic",sans-serif;font-size:13px;line-height:13px}
.name{font-family:"League Gothic",sans-serif;font-weight:400;font-size:13px;line-height:13px;letter-spacing:.3px}
.price{color:var(--basil-light);font-family:"League Gothic",sans-serif;font-weight:400}
.desc{font-size:9px;line-height:10.5px}
.desc .price{font-size:11px}
.flame{display:inline-block;width:7px;height:9px;vertical-align:0}

.extras{position:absolute;left:398px;top:346px;width:402px;height:118px;background:var(--basil);border-radius:2px 6px 6px 2px}
.extras ul{list-style:none;padding:9px 0 0 16px;color:#fff;font-family:"League Gothic",sans-serif;font-size:12.5px;line-height:11.8px;letter-spacing:.3px}
.extras li::before{content:"•";margin-right:4px}
.extras .light{color:#e9f5dc}
.photo{position:absolute}
.bowl{left:600px;top:342px;width:136px;height:136px;border-radius:50%;background:radial-gradient(circle at 45% 40%,#c98a6e 0 18%,#d9b98a 30%,#a7b86a 50%,#e8e0c8 62%,#f5f1e8 70%)}
.plate{left:1032px;top:228px;width:136px;height:98px;border:3px solid var(--basil);border-radius:10px;background:linear-gradient(135deg,#e8b46a,#d98a4e 45%,#f0d49a 70%,#8bb85a)}
</style>
</head>
<body>
<div class="menu">

  <div class="leaf" role="img" aria-label="Watercolor leaf decoration" style="left:60px;top:-40px;width:320px;height:180px"></div>
  <div class="leaf" role="img" aria-label="Watercolor leaf decoration" style="left:-60px;top:420px;width:260px;height:360px"></div>
  <div class="leaf" role="img" aria-label="Watercolor leaf decoration" style="left:940px;top:-30px;width:300px;height:260px"></div>
  <div class="leaf" role="img" aria-label="Watercolor leaf decoration" style="left:1060px;top:520px;width:200px;height:280px"></div>
  <div class="leaf" role="img" aria-label="Watercolor leaf decoration" style="left:700px;top:300px;width:160px;height:120px"></div>

  <!-- Appetizers -->
  <div class="head" style="left:128px;top:22px"><h2 class="section-title" style="font-size:48px">APPETIZERS</h2></div>
  <p class="intro" style="left:29px;top:74px;width:350px">Spring rolls (2) comes with lettuce, vermicelli noodles rolled in rice paper served with peanut sauce with choice of: (cannot be mixed):</p>
  <ol class="list" style="left:40px;top:106px;width:165px">
    <li class="item"><span class="num">1.</span><div><h3 class="name">GOI CUON TOM &amp; THIT HEO <span class="price">4.50</span></h3><p class="desc">Shrimp &amp; pork spring rolls</p></div></li>
    <li class="item"><span class="num">2.</span><div><h3 class="name">GOI CUON THIT HEO / GA /<br>OR BO NUONG <span class="price">5.50</span></h3><p class="desc">Choice of: grilled pork / grilled chicken or grilled beef spring rolls</p></div></li>
    <li class="item"><span class="num">3.</span><div><h3 class="name">BI CUON <span class="price">4.50</span></h3><p class="desc">Pork skin roasted with rice powder spring rolls</p></div></li>
    <li class="item"><span class="num">4.</span><div><h3 class="name">CHA GIO (2) <span class="price">4.50</span></h3><p class="desc">Fried eggrolls with shrimp, pork &amp; vegetables rolled in egg wrap</p></div></li>
    <li class="item"><span class="num">5.</span><div><h3 class="name">CANH GA NUOC MAM (6) <span class="price">7.95</span></h3><p class="desc">Fried chicken wings</p></div></li>
  </ol>
  <ol class="list" style="left:210px;top:106px;width:160px">
    <li class="item"><span class="num">6.</span><div><h3 class="name">GIO TOM (4) <span class="price">5.95</span></h3><p class="desc">Fried shrimp rolls</p></div></li>
    <li class="item"><span class="num">7.</span><div><h3 class="name">CA VIEN CHIEN (8) <span class="price">4.95</span></h3><p class="desc">Fried fish balls</p></div></li>
    <li class="item"><span class="num">8.</span><div><h3 class="name">CHAO TOM (2) <span class="price">7.95</span></h3><p class="desc">Grilled shrimp paste wrapped around sugar cane stick</p></div></li>
    <li class="item"><span class="num">9.</span><div><h3 class="name">WONTON SOUP</h3><p class="desc"><span class="price">(CUP) 4.95 (BOWL) 7.50</span><br>Wonton shrimp &amp; pork soup</p></div></li>
    <li class="item"><span class="num">10.</span><div><h3 class="name">TOM CUA SOUP</h3><p class="desc"><span class="price">(CUP) 4.95 (BOWL) 7.50</span><br>Crab meat, shrimp &amp; egg soup</p></div></li>
  </ol>

  <p class="intro" style="left:29px;top:310px;width:340px">Vietnamese salad comes with thin cabbage, carrots, onions, mints, crushed peanuts tossed in lime juice &amp; vinegar with the following choices of:</p>
  <ol class="list" style="left:40px;top:336px;width:160px">
    <li class="item"><span class="num">11.</span><div><h3 class="name">GOI GA <span class="price">8.95</span></h3><p class="desc">Chicken salad</p></div></li>
    <li class="item"><span class="num">12.</span><div><h3 class="name">GOI TOM <span class="price">9.95</span></h3><p class="desc">Shrimp salad</p></div></li>
  </ol>
  <ol class="list" style="left:210px;top:338px;width:160px">
    <li class="item"><span class="num">13.</span><div><h3 class="name">BO TAI CHANH <span class="price">11.95</span></h3><p class="desc">Rare thin sliced beef with onions, mints, basils, crushed peanuts in lime juice &amp; vinegar</p></div></li>
    <li class="item"><span class="num">14.</span><div><h3 class="name">CHIM CUT ROTI <span class="price">11.95</span></h3><p class="desc">Roasted quails served with salt &amp; pepper</p></div></li>
  </ol>

  <!-- Hu tieu -->
  <div class="head stack left" style="left:30px;top:410px">
    <h2 class="section-title" style="font-size:46px">HU TIEU (MI)</h2>
    <div class="head-text">
      <p class="subtitle">RICE OR EGG NOODLE SOUP</p>
      <p class="note">In pork broth</p>
    </div>
  </div>
  <ol class="list" style="left:40px;top:486px;width:325px">
    <li class="item"><span class="num">15.</span><div><h3 class="name">HU TIEU (MI) DAC BIET <span class="price">10.50</span></h3><p class="desc">Choice of: rice or egg noodle with shrimp, roast pork, chicken, imitation crab, quail eggs, ground pork &amp; fried shrimp cracker combination noodle soup</p></div></li>
    <li class="item"><span class="num">16.</span><div><h3 class="name">HU TIEU (MI) HAI SAN <span class="price">11.50</span></h3><p class="desc">Choice of: rice or egg noodle with shrimp, scallop, squid, fish balls &amp; imitation crab seafood noodle soup</p></div></li>
    <li class="item"><span class="num">17.</span><div><h3 class="name">HU TIEU MYTHO <span class="price">9.95</span></h3><p class="desc">Shrimp, roast pork, chicken, fish ball, imitation crab &amp; ground pork with clear noodle soup</p></div></li>
    <li class="item"><span class="num">18.</span><div><h3 class="name">HU TIEU SATE <span class="price">9.50</span> <svg class="flame" viewBox="0 0 7 9"><path fill="var(--flame)" d="M3.5 0C4 2 6.5 3 6.5 5.6A3 3 0 0 1 .5 5.6C.5 4 2 3.4 2 2c1 .8 1.4 1.6 1.5 0z"/></svg></h3><p class="desc">Beef with tomato slices, cucumber, bean sprouts &amp; crushed peanuts in spicy noodle soup</p></div></li>
  </ol>
  <ol class="list" style="left:40px;top:652px;width:165px">
    <li class="item"><span class="num">19.</span><div><h3 class="name">HU TIEU (MI) KHO DAC BIET <span class="price">10.95</span></h3><p class="desc">Choice of: rice or egg noodle with shrimp, roast pork, chicken, imitation crab, ground pork and fried shrimp cracker with soup on the side</p></div></li>
    <li class="item"><span class="num">20.</span><div><h3 class="name">MI HOANH THANH <span class="price">8.95</span></h3><p class="desc">Wonton with egg noodle soup<br>+XA XIU (roast pork) <span class="price">9.95</span></p></div></li>
  </ol>
  <ol class="list" style="left:210px;top:652px;width:160px">
    <li class="item"><span class="num">21.</span><div><h3 class="name">BANH CANH TOM<br>THIT GIO HEO <span class="price">9.50</span></h3><p class="desc">Shrimp, pork knuckle &amp; Vietnamese big noodle soup</p></div></li>
    <li class="item"><span class="num">22.</span><div><h3 class="name">BANH CANH GA <span class="price">8.95</span></h3><p class="desc">Chicken with Vietnamese big noodle soup</p></div></li>
  </ol>

  <!-- Pho -->
  <div class="head stack" style="left:540px;top:22px;width:120px">
    <h2 class="section-title" style="font-size:46px">PHO</h2>
    <p class="subtitle">RICE NOODLES SOUP</p>
  </div>
  <ol class="list" style="left:440px;top:107px;width:165px">
    <li class="item"><span class="num">23.</span><div><h3 class="name">PHO DAC BIET <span class="price">9.50</span></h3><p class="desc">Steak, brisket, flank, tendon, tripe &amp; meatballs combination noodle soup</p></div></li>
    <li class="item"><span class="num">24.</span><div><h3 class="name">PHO <span class="price">8.50</span></h3><p class="desc">Noodle soup with choices up to 3 items: steak, brisket, flank, tendon, tripe, meatball or vegetables</p></div></li>
    <li class="item"><span class="num">25.</span><div><h3 class="name">PHO GA VIETNAM (GA DI BO) <span class="price">10.50</span></h3><p class="desc">Free range chicken noodle soup</p></div></li>
    <li class="item"><span class="num">26.</span><div><h3 class="name">PHO GA MY <span class="price">9.50</span></h3><p class="desc">White chicken &amp; mixed vegetables noodle soup</p></div></li>
    <li class="item"><span class="num">27.</span><div><h3 class="name">PHO THIT HEO / BO /<br>OR GA NUONG <span class="price">10.50</span></h3><p class="desc">Choice of: grilled pork, grilled beef or grilled chicken with mixed vegetables noodle soup</p></div></li>
  </ol>
  <ol class="list" style="left:610px;top:107px;width:170px">
    <li class="item"><span class="num">28.</span><div><h3 class="name">PHO DO BIEN <span class="price">11.50</span></h3><p class="desc">Shrimp, scallop, squid, fish balls, imitation crab &amp; vegetables seafood noodle soup</p></div></li>
    <li class="item"><span class="num">29.</span><div><h3 class="name">PHO TOM <span class="price">9.95</span></h3><p class="desc">Shrimp with mixed vegetables noodle soup</p></div></li>
    <li class="item"><span class="num">30.</span><div><h3 class="name">PHO DO BIEN CHUA CAY <span class="price">11.50</span> <svg class="flame" viewBox="0 0 7 9"><path fill="var(--flame)" d="M3.5 0C4 2 6.5 3 6.5 5.6A3 3 0 0 1 .5 5.6C.5 4 2 3.4 2 2c1 .8 1.4 1.6 1.5 0z"/></svg></h3><p class="desc">Shrimp, scallop, squid, fish balls &amp; imitation crab in hot &amp; sour seafood noodle soup</p></div></li>
    <li class="item"><span class="num">31.</span><div><h3 class="name">PHO TRE EM <span class="price">7.50</span></h3><p class="desc">Kid's steak &amp; meatball noodle soup</p></div></li>
  </ol>

  <div class="extras">
    <ul>
      <li>X-LARGE <span class="light">2.00 MORE</span></li>
      <li>EXTRA MEAT <span class="light">(STEAK, CHICKEN, ETC.) 3.50</span></li>
      <li>EXTRA SHRIMP <span class="light">3.00</span></li>
      <li>EXTRA HERBS OR VEGETABLES <span class="light">1.50<br>&nbsp;&nbsp;(EX: CILANTROS, BASILS, BEANSPROUTS, ETC.)</span></li>
      <li>EXTRA RICE, SOUP OR NOODLES <span class="light">1.50</span></li>
      <li>CHANGE NOODLE OR BROWN RICE <span class="light">2.00</span></li>
      <li>ADD FRIED EGG <span class="light">1.50</span></li>
      <li>ADD OR CHANGE TO FRIED RICE <span class="light">3.00</span></li>
    </ul>
  </div>
  <div class="photo bowl" role="img" aria-label="Photo of a bowl of pho with rare beef, noodles and scallions"></div>

  <!-- Bun -->
  <div class="head" style="left:413px;top:476px">
    <h2 class="section-title" style="font-size:44px">BUN</h2>
    <div class="head-text" style="width:330px">
      <p class="subtitle">VERMICELLI NOODLE BOWL</p>
      <p class="note faint">All vermicelli bowl comes with fresh lettuce, bean sprouts, sliced cucumbers, shredded carrots &amp; crushed peanuts</p>
    </div>
  </div>
  <ol class="list" style="left:437px;top:535px;width:165px">
    <li class="item"><span class="num">32.</span><div><h3 class="name">BUN DAC BIET <span class="price">12.95</span></h3><p class="desc">Choice of: grilled pork, grilled chicken or grilled beef with grilled shrimp &amp; fried eggroll special combination vermicelli bowl</p></div></li>
    <li class="item"><span class="num">33.</span><div><h3 class="name">BUN - VERMICELLI BOWL <span class="price">9.50</span></h3><p class="desc">Choice of: grilled pork, grilled chicken or grilled beef<br>+ EGGROLL <span class="price">9.95</span><br>+ SHRIMP <span class="price">10.50</span></p></div></li>
    <li class="item"><span class="num">34.</span><div><h3 class="name">BUN TOM NUONG (8) <span class="price">10.95</span></h3><p class="desc">Grilled shrimp vermicelli bowl</p></div></li>
  </ol>
  <ol class="list" style="left:608px;top:535px;width:170px">
    <li class="item"><span class="num">35.</span><div><h3 class="name">BUN CHA GIO (3) <span class="price">9.50</span></h3><p class="desc">Fried eggroll vermicelli bowl</p></div></li>
    <li class="item"><span class="num">36.</span><div><h3 class="name">BUN CHAO TOM (2) <span class="price">9.50</span></h3><p class="desc">Grilled shrimp paste vermicelli bowl</p></div></li>
    <li class="item"><span class="num">37.</span><div><h3 class="name">BUN BO HUE <span class="price">9.50</span> <svg class="flame" viewBox="0 0 7 9"><path fill="var(--flame)" d="M3.5 0C4 2 6.5 3 6.5 5.6A3 3 0 0 1 .5 5.6C.5 4 2 3.4 2 2c1 .8 1.4 1.6 1.5 0z"/></svg></h3><p class="desc">Spicy beef noodle soup with beef shank, pork knuckle, pork blood with large vermicelli noodles</p></div></li>
    <li class="item"><span class="num">38.</span><div><h3 class="name">BUN RIEU <span class="price">9.50</span></h3><p class="desc">Mixed ground pork &amp; crab, pork blood, dried tofu with vermicelli rice noodle in tomato broth soup</p></div></li>
    <li class="item"><span class="num">39.</span><div><h3 class="name">BUN MANG VIT <span class="price">9.50</span></h3><p class="desc">Duck &amp; bamboo vermicelli noodle soup</p></div></li>
  </ol>

  <!-- Com tam -->
  <div class="head stack" style="left:930px;top:22px;width:140px">
    <h2 class="section-title" style="font-size:46px">COM TAM</h2>
    <p class="subtitle">BROKEN RICE PLATE</p>
  </div>
  <ol class="list" style="left:838px;top:98px;width:330px">
    <li class="item"><span class="num">40.</span><div><h3 class="name">COM DAC BIET <span class="price">14.95</span></h3><p class="desc">Special rice combination with grilled chicken, grilled pork, grilled shrimp &amp; fried eggroll</p></div></li>
    <li class="item"><span class="num">41.</span><div><h3 class="name">COM SUON NUONG XA <span class="price">9.95</span></h3><p class="desc">Grilled pork chops marinated in lemongrass</p></div></li>
    <li class="item"><span class="num">42.</span><div><h3 class="name">COM SUON BI CHA <span class="price">9.50</span></h3><p class="desc">Grilled pork chop, pork skin roasted with rice powder &amp; eggcake</p></div></li>
    <li class="item" style="width:190px"><span class="num">43.</span><div><h3 class="name">COM THIT NUONG, GA NUONG OR BO NUONG <span class="price">9.75</span></h3><p class="desc">Choice of: grilled pork, grilled chicken or grilled beef<br>+SHRIMP <span class="price">10.95</span></p></div></li>
    <li class="item"><span class="num">44.</span><div><h3 class="name">COM SUON DAI HAN <span class="price">13.95</span></h3><p class="desc">Grilled Korean BBQ ribs</p></div></li>
  </ol>
  <div class="photo plate" role="img" aria-label="Photo of a plate of fried rice with egg, peas and carrots"></div>

  <!-- Com chien -->
  <div class="head" style="left:810px;top:318px">
    <h2 class="section-title" style="font-size:44px">COM CHIEN</h2>
    <div class="head-text" style="width:105px">
      <p class="subtitle">FRIED RICE</p>
      <p class="note faint">Fried rice is cooked with egg, peas &amp; carrots</p>
    </div>
  </div>
  <ol class="list" style="left:835px;top:374px;width:165px">
    <li class="item"><span class="num">45.</span><div><h3 class="name">COM CHIEN THAP CAM <span class="price">10.95</span></h3><p class="desc">House special fried rice with shrimp, roasted pork, sausage with peas &amp; carrots</p></div></li>
    <li class="item"><span class="num">46.</span><div><h3 class="name">COM CHIEN TOM <span class="price">9.95</span></h3><p class="desc">Shrimp fried rice</p></div></li>
    <li class="item"><span class="num">47.</span><div><h3 class="name">COM CHIEN GA <span class="price">9.95</span></h3><p class="desc">Chicken fried rice</p></div></li>
  </ol>
  <ol class="list" style="left:1005px;top:374px;width:170px">
    <li class="item"><span class="num">48.</span><div><h3 class="name">COM CHIEN CANH GA <span class="price">9.50</span></h3><p class="desc">Fried rice with fried chicken wings</p></div></li>
    <li class="item"><span class="num">49.</span><div><h3 class="name">COM CHIEN BO LUC LAC <span class="price">14.50</span></h3><p class="desc">Shaking beef stir fry filet mignon with bell peppers with fried rice<br>+ SHRIMP <span class="price">16.95</span></p></div></li>
  </ol>

  <!-- Xao -->
  <div class="head" style="left:810px;top:496px">
    <h2 class="section-title" style="font-size:44px">XAO</h2>
    <div class="head-text">
      <p class="subtitle">STIR FRY<br>WITH RICE<br>PLATE</p>
    </div>
  </div>
  <ol class="list" style="left:835px;top:550px;width:165px">
    <li class="item"><span class="num">50.</span><div><h3 class="name">GA XAO GUNG <span class="price">10.95</span></h3><p class="desc">Stir fry chicken with ginger</p></div></li>
    <li class="item"><span class="num">51.</span><div><h3 class="name">GA OR BO XAO XA OT <span class="price">10.95</span> <svg class="flame" viewBox="0 0 7 9"><path fill="var(--flame)" d="M3.5 0C4 2 6.5 3 6.5 5.6A3 3 0 0 1 .5 5.6C.5 4 2 3.4 2 2c1 .8 1.4 1.6 1.5 0z"/></svg></h3><p class="desc">Choice of: stir fry chicken or beef in hot chili &amp; lemongrass</p></div></li>
    <li class="item"><span class="num">52.</span><div><h3 class="name">TOM XAO XA OT <span class="price">11.95</span> <svg class="flame" viewBox="0 0 7 9"><path fill="var(--flame)" d="M3.5 0C4 2 6.5 3 6.5 5.6A3 3 0 0 1 .5 5.6C.5 4 2 3.4 2 2c1 .8 1.4 1.6 1.5 0z"/></svg></h3><p class="desc">Stir fry shrimp in hot chilli &amp; lemongrass</p></div></li>
    <li class="item"><span class="num">53.</span><div><h3 class="name">GA OR BO XAO RAU CAI <span class="price">10.95</span></h3><p class="desc">Choice of: stir fry chicken or beef with mixed vegetables</p></div></li>
    <li class="item"><span class="num">54.</span><div><h3 class="name">TOM XAO RAU CAI <span class="price">11.95</span></h3><p class="desc">Stir fry shrimp with mixed vegetables</p></div></li>
  </ol>
  <ol class="list" style="left:1005px;top:550px;width:170px">
    <li class="item"><span class="num">55.</span><div><h3 class="name">MI XAO MEM OR DON HAI SAN <span class="price">15.95</span></h3><p class="desc">Choice of: soft or crispy noodles stir fry with shrimp, squid, fish ball &amp; imitation crab with vegetables</p></div></li>
    <li class="item"><span class="num">56.</span><div><h3 class="name">COM TOM RANG CHAY MO <span class="price">12.95</span></h3><p class="desc">Stir fry shrimp, ginger, onion &amp; bell pepper in garlic sauce</p></div></li>
    <li class="item"><span class="num">57.</span><div><h3 class="name">CANH CHUA CA OR TOM <span class="price">15.95</span></h3><p class="desc">Choice of: fish or shrimp soup with tomato, pineapple, okra &amp; bean sprouts served with white rice (serving 2-4)</p></div></li>
    <li class="item"><span class="num">58.</span><div><h3 class="name">CA KHO TO <span class="price">15.95</span></h3><p class="desc">Braised swai fish in clay pot with black pepper &amp; dry shallots served with white rice</p></div></li>
  </ol>

</div>
</body>
</html>
```